Corporate website design needed

We need a Contemporary Industrial/Tech/Logistics Website design to match our logistic client's business. Our client consults and build logistics solutions that they manage but they are not a typical 3PL (3rd party logistics company) which is primarily engaged in moving boxes.
PSD file only for now, home and default templates.
COMPANY CHARACTER
DESIGN LOOK AND FEEL
• The design should also be modern and visually well organized — employing a combination of visual devices and info graphics. Keep it light and not too heavy but strong/ professional. And unique.
• The design should go beyond the typical industrial pick and pack 3PL representing [Logistics Company] as a High Tech/IT logistics company.
Some examples although these are not right for this client because they have much more content and present themselves more as a 3pl.
http://www.vobrelink-hub.example/ (More right then wrong - Like this but simplified)
http://www.durmaxfreight.example (Ugly)
http://www.tpwallerton.example (More right then wrong but different focus)
http://www.pelhamrye.example/ Too 3PL trucking… We want a bit ore high level approach
The difference, the design should be a fusion in core concepts that culminate in a design which implies the following attributes. Tech (Big data / analytics / software), Consultancy (Solutions, SME, Leader), 3PL Industry vertical solutions.
NOTE: The visualization of “tech” is not “1” and “0”, but more “software and analytics” Perhaps more like www.navimetra.example.
• They need to be seen as a solutions provider in Logistics and as in Subject matter experts
TONE
The tone needs to exude professionalism, expertise, though leadership along with technical and executional excellence.
Experienced
Knowledgeable
Confident
Determined
Straightforward
WEBSITE OBJECTIVES
• Focus C-Suite executives and logistics managers’ attention on [Logistics Company]s commanding knowledge and expertise, and unique approach to supply chain solutions producing more RFP wins
• Create an easy to scan design which decreases the reliance on text through featured text, summaries, and smaller “chunked” size bits of information.
• Convey [Logistics Company] as high-tech 3PL solutions developer and services provider with a ‘high-touch’ consultative approach.
• Showcase [Logistics Company]’s value propositions. (See Slider Content)
• Showcase [Logistics Company]’s expertise in logistical analytics.
• Gain recognition as an industry leader in evolutionary new space (supply chain 2.0)
WEBSITE STRATEGY
• Reduce reliance on text (at least within initial entry points for each section)
• Typography: Watch text line lengths and readability, bolder fonts. NO SERIFS
• Generally, create a click-through format so that users who want more details can find it, and those who don’t can get a snapshot without clicking through.
• Increase visual content through info graphics and some dynamic content, photography
• Better utilize the space on each page (e.g., add visual interest, photography and iconography where appropriate to break up copy blocks and maintain readable line lengths).
COLOR SCHEME
• Create a more engaging color scheme (the logo will remain the same under all circumstances).
• Red / grayscale may work…. Not too dark or heavy. Not too much red. Ex. quiltora.example
• Also try blues and greys. They seem to like that. Open to suggestions but don’t get to crazy. Red is in their logo but too much may be a problem.
PHOTOGRAPHY
Yes. And I will upload some.
If you pick photography please be sure to note Which stock house used and the image number!
CONTENT
The content will be presented in a more hierarchical format — with lead-ins, paragraph and section headers and navigational cues to expand lengthier content allowing the visitor to more easily scan the website. No case studies, No Social media, News while on the home page should not be over emphasized. They don't post a lot so it gets dated quickly ...
I will be uploading a wire frame and other elements.
NOTE: I uploaded my EXAMPLE mock up which is close but not close enough.
I am not a great designer. So I am looking for an alternative that exceed my design ability! These examples show the basic layout but I really want some varied alternatives.
The colors are inconsistent and type not quite right. The grey bar at top is not right and should probably go away.
Please pull the basic elements in the example together into a great design.
If you have questions please contact me.
i will upload some photography tomorrow that may be of use.
Thanks!
Updates
Hi All,
We are still evaluating the submitted designs. Sorry for the delay.
Target Market(s)
This website is primarily a validation website. Few new customers will search and find them as such...
The site should be Focused on C-Suite executives and logistics managers’ attention on [Logistics Company]s commanding knowledge and expertise, and unique approach to supply chain solutions producing more RFP wins
Industry/Entity Type
Business
Font styles to use
Requirements
Must have
- Slide show, Clearly explain who they are and what they do.
Create an easy to scan design which decreases the reliance on text through featured text, summaries, and smaller “chunked” size bits of information.
Convey [Logistics Company] as high-tech 3PL solutions developer and services
provider with a ‘high-touch’ consultative approach.
Should not have
- No Ads space
No Social media
Not too cluttered. Keep it clean.

```html
<!DOCTYPE html>
<html lang="en">
<head>
<meta charset="utf-8">
<title>Kestrel Row Logistics — Home</title>
<link href="https://fonts.googleapis.com/css2?family=Open+Sans:wght@400;600;700;800&display=swap" rel="stylesheet">
<style>
:root{
  --red:#c8102e;
  --red-dark:#9e0c22;
  --ink:#2b2b2b;
  --text:#5a5a5a;
  --muted:#8a8a8a;
  --line:#e2e2e2;
  --band:#ededed;
  --dark:#232323;
  --foot-text:#9c9c9c;
  --white:#ffffff;
}
*{box-sizing:border-box;margin:0;padding:0}
html,body{width:828px;height:1200px;overflow:hidden;background:var(--white)}
body{font-family:"Open Sans",Arial,sans-serif;color:var(--text);font-size:9px;line-height:1.4}
a{color:inherit;text-decoration:none}
.page{width:828px;height:1200px;display:flex;flex-direction:column}

.utility-bar{height:16px;flex:none;background:var(--dark);color:#cfcfcf;font-size:7.5px;display:flex;justify-content:flex-end;align-items:center;padding-right:26px;gap:10px}
.utility-bar .sales{color:var(--white);font-weight:600}

.site-header{height:50px;flex:none;display:flex;align-items:center;justify-content:space-between;padding:0 28px;border-bottom:1px solid var(--line)}
.brand{display:flex;align-items:center;gap:8px}
.brand-dot{width:28px;height:28px;border-radius:50%;background:var(--red)}
.brand-name{font-size:12.5px;font-weight:700;color:var(--ink);letter-spacing:1.5px;text-transform:uppercase}
.main-nav{display:flex;gap:26px;font-size:11px;font-weight:600;color:var(--ink)}

.hero{height:250px;flex:none;position:relative;
  background:
    radial-gradient(ellipse 120px 170px at 56% 78%,rgba(40,40,48,.85),rgba(40,40,48,0) 70%),
    radial-gradient(ellipse 260px 120px at 48% 32%,rgba(255,255,255,.95),rgba(255,255,255,0) 75%),
    linear-gradient(100deg,#1d5fa8 0%,#4f8fcf 14%,#dfe9f3 32%,#f4f6f8 60%,#c7d6e6 82%,#3d78b8 100%)}
.hero-caption{position:absolute;left:40px;bottom:14px;display:flex;align-items:center;background:rgba(30,30,30,.85);color:var(--white);font-size:12px;font-weight:600;padding:4px 10px;gap:8px}
.hero-caption small{font-size:8px;font-weight:400;color:#d6d6d6}
.hero-arrow{position:absolute;top:111px;width:22px;height:28px;background:rgba(20,20,20,.8);display:flex;align-items:center;justify-content:center}
.hero-arrow.prev{left:0}.hero-arrow.next{right:0}

.services{height:190px;flex:none;display:flex;gap:12px;padding:14px 28px 0}
.service-card{flex:1}
.service-thumb{height:66px;margin-bottom:7px}
.service-card h3{font-size:8.5px;color:var(--red);font-weight:700;line-height:1.25;margin-bottom:4px;min-height:22px}
.service-card p{font-size:7px;color:var(--muted);margin-bottom:6px}
.read-more{font-size:7px;font-weight:700;color:var(--ink)}

.approach{height:226px;flex:none;background:var(--band);display:flex;padding:16px 28px;gap:24px}
.approach-photo{width:400px;height:194px;background:linear-gradient(180deg,#e4e4e4 0%,#b9b9b9 45%,#6e6e6e 100%)}
.approach-list{flex:1;display:flex;flex-direction:column;gap:22px;padding-top:10px}
.approach-item{display:flex;gap:8px}
.approach-icon{width:20px;height:20px;background:var(--red);flex:none}
.approach-item h4{font-size:8.5px;font-weight:700;color:var(--red);text-transform:uppercase;margin-bottom:2px}
.approach-item p{font-size:7px;color:var(--text)}

.lower{flex:1;display:flex;padding:20px 28px 18px;gap:30px}
.news{width:250px;border-top:1px solid var(--line);padding-top:12px;display:flex;flex-direction:column}
.section-title{font-size:9px;font-weight:700;color:var(--red);text-transform:uppercase;margin-bottom:12px}
.news-item{display:flex;gap:6px;margin-bottom:18px}
.news-item .bullet{width:6px;height:6px;background:var(--red);margin-top:3px;flex:none}
.news-item h5{font-size:7.5px;font-weight:700;color:var(--ink);margin-bottom:3px}
.news-item p{font-size:6.8px;color:var(--muted)}
.btn-red{align-self:flex-end;background:var(--red);color:var(--white);font-size:7px;font-weight:600;padding:3px 8px;margin-top:auto}
.perspective{flex:1;border-top:1px solid var(--line);padding-top:12px;display:flex;flex-direction:column}
.perspective h3{font-size:9px;font-weight:700;color:var(--ink);text-transform:uppercase;margin-bottom:10px}
.perspective ul{list-style:none;margin-bottom:16px}
.perspective li{font-size:7.5px;color:var(--text);padding-left:10px;position:relative;margin-bottom:5px}
.perspective li::before{content:"";position:absolute;left:0;top:4px;width:4px;height:4px;background:var(--red)}
.contact-box{display:flex;background:var(--band);flex:1}
.contact-label{width:110px;display:flex;align-items:center;justify-content:center;font-size:9px;font-weight:700;color:var(--red);border-right:1px solid #d6d6d6}
.contact-body{padding:16px 14px;font-size:7.5px;color:var(--text);line-height:1.6}
.contact-body strong{display:block;color:var(--ink);font-weight:700}

.site-footer{height:172px;flex:none;background:var(--dark);display:flex;gap:20px;padding:16px 28px 0}
.footer-col{flex:1}
.footer-col h6{font-size:7.5px;font-weight:700;color:var(--white);margin-bottom:7px}
.footer-col li{list-style:none;font-size:6.5px;color:var(--foot-text);line-height:1.9}
.copyright{height:18px;flex:none;background:var(--red-dark);color:#f2d0d5;font-size:6.5px;display:flex;align-items:center;justify-content:center}
</style>
</head>
<body>
<div class="page">

  <div class="utility-bar">
    <a href="#">Company</a><a href="#">Careers</a><a href="#">Contact</a><a href="#">Search</a>
    <span class="sales">Sales: 800-555-0142</span>
  </div>

  <header class="site-header">
    <div class="brand"><span class="brand-dot"></span><span class="brand-name">Kestrel Row Logistics</span></div>
    <nav class="main-nav"><a href="#">Solutions</a><a href="#">Our Process</a><a href="#">Industries</a></nav>
  </header>

  <section class="hero" role="img" aria-label="Businessman drawing analytics charts and diagrams on a glass board against a blue sky">
    <span class="hero-arrow prev"><svg width="8" height="12" viewBox="0 0 8 12"><path d="M6 1 1 6l5 5" fill="none" stroke="#fff" stroke-width="2"/></svg></span>
    <span class="hero-arrow next"><svg width="8" height="12" viewBox="0 0 8 12"><path d="M2 1l5 5-5 5" fill="none" stroke="#fff" stroke-width="2"/></svg></span>
    <div class="hero-caption">Delivering real business growth <small>through supply chain excellence</small></div>
  </section>

  <section class="services">
    <article class="service-card">
      <div class="service-thumb" role="img" aria-label="Factory floor with materials" style="background:linear-gradient(135deg,#c9a46b,#6d5a3c)"></div>
      <h3>Material Management &amp; Factory Support</h3>
      <p>Our unique 3D network and logistics systems keep lines moving.</p>
      <a class="read-more" href="#">READ MORE &gt;</a>
    </article>
    <article class="service-card">
      <div class="service-thumb" role="img" aria-label="Retail shopping scene" style="background:linear-gradient(135deg,#9cc0e0,#3d6b96)"></div>
      <h3>Retail and e-Commerce Distribution</h3>
      <p>Our unique 3D network and logistics systems serve every channel.</p>
      <a class="read-more" href="#">READ MORE &gt;</a>
    </article>
    <article class="service-card">
      <div class="service-thumb" role="img" aria-label="Aftermarket parts warehouse" style="background:linear-gradient(135deg,#b9bcc0,#5b6168)"></div>
      <h3>Aftermarket Support</h3>
      <p>Our unique 3D network and logistics systems manage parts flows.</p>
      <a class="read-more" href="#">READ MORE &gt;</a>
    </article>
    <article class="service-card">
      <div class="service-thumb" role="img" aria-label="Critical logistics operations" style="background:linear-gradient(135deg,#d0d6db,#7c8690)"></div>
      <h3>Critical Logistics</h3>
      <p>Our unique 3D network and logistics systems move urgent goods.</p>
      <a class="read-more" href="#">READ MORE &gt;</a>
    </article>
    <article class="service-card">
      <div class="service-thumb" role="img" aria-label="Supply chain planning meeting" style="background:linear-gradient(135deg,#c99a8a,#7a4b40)"></div>
      <h3>Supply Chain Transformation Services</h3>
      <p>Our unique 3D network and logistics systems reshape networks.</p>
      <a class="read-more" href="#">READ MORE &gt;</a>
    </article>
  </section>

  <section class="approach">
    <div class="approach-photo" role="img" aria-label="Business team standing in a bright office, seen in silhouette"></div>
    <div class="approach-list">
      <div class="approach-item"><span class="approach-icon"></span><div>
        <h4>A Different Incentive</h4>
        <p>We commit our own capital and resources to align with our clients' goals.</p></div></div>
      <div class="approach-item"><span class="approach-icon"></span><div>
        <h4>A Different Approach</h4>
        <p>Unlike consultants, we implement and operate the solutions we design.</p></div></div>
      <div class="approach-item"><span class="approach-icon"></span><div>
        <h4>A Different Level of Commitment</h4>
        <p>We guarantee business performance for our clients by investing in and executing the solutions we design.</p></div></div>
    </div>
  </section>

  <section class="lower">
    <div class="news">
      <h3 class="section-title">Recent News</h3>
      <div class="news-item"><span class="bullet"></span><div>
        <h5>Kestrel Row Continues to Fly High with Record Donations</h5>
        <p>Marlow Point, NC — March 2014 — Our team raised record funds for local charities again this spring season, thanks to every site.</p></div></div>
      <div class="news-item"><span class="bullet"></span><div>
        <h5>Kestrel Row Logistics Ranked #1 in Distribution Operations in the Region</h5>
        <p>Marlow Point, NC — May 2014 — A regional survey names our sites top performers for quality, safety and service.</p></div></div>
      <a class="btn-red" href="#">Read More</a>
    </div>
    <div class="perspective">
      <h3>A Different Perspective</h3>
      <ul>
        <li>We commit our own capital and resources to align with our clients' goals</li>
        <li>Unlike consultants, we implement and operate the solutions we design</li>
        <li>We guarantee business performance for our clients by investing in and executing the solutions we design</li>
      </ul>
      <div class="contact-box">
        <div class="contact-label">CONTACT US</div>
        <div class="contact-body">
          <strong>General Contact &nbsp;Careers &nbsp;Media Relations Contact</strong>
          <strong>Sales Inquiries: 800-555-0142</strong><br>
          Kestrel Row Logistics, 210 Larkfield Way<br>Marlow Point, NC 27000
        </div>
      </div>
    </div>
  </section>

  <footer class="site-footer">
    <div class="footer-col"><h6>Our Process</h6><ul>
      <li>Concept &amp; Systems</li><li>Engineering Solutions</li><li>Implementation Plans</li><li>Operating Excellence</li><li>Continuous Improvement</li><li>Performance Review</li><li>Shared Risk Models</li><li>Working with Us</li></ul></div>
    <div class="footer-col"><h6>Our Solutions</h6><ul>
      <li>Material Management</li><li>Retail Distribution</li><li>Aftermarket Support</li><li>Critical Logistics</li><li>Transformation Services</li><li>Technology</li><li>Quality</li></ul></div>
    <div class="footer-col"><h6>Industries We Serve</h6><ul>
      <li>Aerospace</li><li>Consumer Goods</li><li>Government</li><li>Healthcare</li><li>Manufacturing</li><li>Retail &amp; Apparel</li><li>Telecom</li><li>Medical</li></ul></div>
    <div class="footer-col"><h6>Company</h6><ul>
      <li>About Us</li><li>Leadership Team</li><li>Careers</li><li>News &amp; Media</li><li>Locations</li><li>Contact</li></ul></div>
  </footer>
  <div class="copyright">Copyright © 2014 All Rights Reserved</div>
</div>
</body>
</html>
```